Computer consultant business card

Bexil Software is a newly started computer consulting company. It's a small one-man company that provides mostly Vornix applications but also websites in collaboration with designers. I'm running this company on the side of full time university studies.

I want the final design to be clean and memorable. Be creative! :)

Some inspiration:
http://www.pixelmarta.com/design/48317
http://www.pixelmarta.com/design/2739164/business-card-design-by-frostlynk
http://www.pixelmarta.com/design/604281/business-card-design-by-koralind-vestrabanu

See attachment for my company logo.
Updates

I would like to thank everyone for submitting! I'll need a couple of days to review and ultimately select a design.

Target Market(s)

Non-technical entrepreneurs and small companies.

Industry/Entity Type

University

Requirements
Must have
• My company logo.
In any way, both colors from my logo.
First- and last name, e-mail and phone number.
Double-sided design.
Nice to have
• Something creative with the symbol in my logo

```html
<!DOCTYPE html>
<html lang="en">
<head>
<meta charset="utf-8">
<title>Lurvex – Business Card</title>
<link rel="stylesheet" href="https://fonts.googleapis.com/css2?family=Arimo:wght@400;700&display=swap">
<style>
  :root {
    --backdrop: #e9e6e1;
    --card-white: #ffffff;
    --brand-dark: #333132;
    --brand-blue: #1f78f0;
    --text-light: #ffffff;
  }
  * { box-sizing: border-box; margin: 0; padding: 0; }
  html, body {
    width: 1200px;
    height: 823px;
    overflow: hidden;
    background: var(--backdrop);
    font-family: "Arimo", Arial, sans-serif;
  }
  .stage {
    position: relative;
    width: 1200px;
    height: 823px;
  }
  .card {
    position: absolute;
    top: 251px;
    width: 540px;
    height: 320px;
    border-radius: 18px;
    overflow: hidden;
    box-shadow: 0 6px 18px rgba(0,0,0,0.18);
  }

  /* Front */
  .card-front {
    left: 40px;
    background: var(--card-white);
    display: flex;
    flex-direction: column;
  }
  .front-brand {
    height: 184px;
    display: flex;
    align-items: center;
    padding-left: 58px;
    gap: 22px;
  }
  .brand-dot {
    flex: none;
    width: 96px;
    height: 96px;
    border-radius: 50%;
    background: var(--brand-blue);
  }
  .brand-name {
    font-weight: 700;
    font-size: 80px;
    letter-spacing: 1px;
    color: var(--brand-dark);
    line-height: 1;
    white-space: nowrap;
  }
  .front-contact {
    position: relative;
    height: 80px;
    background: var(--brand-dark);
    display: flex;
    align-items: center;
    justify-content: center;
    gap: 14px;
    padding-top: 6px;
    color: var(--text-light);
  }
  .front-contact::before {
    content: "";
    position: absolute;
    top: 0;
    right: 0;
    width: 46%;
    height: 9px;
    background: var(--brand-blue);
  }
  .person {
    text-align: right;
    line-height: 1.15;
  }
  .person-first { font-weight: 700; font-size: 20px; display: block; }
  .person-last { font-size: 16px; display: block; }
  .divider {
    width: 2px;
    height: 40px;
    background: var(--text-light);
  }
  .details {
    list-style: none;
    font-size: 14px;
    line-height: 1.5;
  }
  .details li { display: flex; align-items: center; gap: 6px; white-space: nowrap; }
  .details svg { width: 12px; height: 12px; fill: var(--text-light); }
  .front-address {
    flex: 1;
    background: var(--brand-blue);
    color: var(--text-light);
    font-size: 15px;
    letter-spacing: 1.5px;
    display: flex;
    align-items: center;
    justify-content: center;
  }

  /* Back */
  .card-back {
    left: 620px;
    background: var(--brand-dark);
    display: flex;
    align-items: center;
    justify-content: center;
    gap: 20px;
  }
  .card-back .brand-dot { background: var(--text-light); width: 80px; height: 80px; }
  .card-back .brand-name { color: var(--text-light); font-size: 68px; }
</style>
</head>
<body>
<main class="stage">
  <section class="card card-front" aria-label="Business card front">
    <div class="front-brand">
      <span class="brand-dot"></span>
      <span class="brand-name">lurvex</span>
    </div>
    <div class="front-contact">
      <div class="person">
        <span class="person-first">First Name</span>
        <span class="person-last">Last Name</span>
      </div>
      <span class="divider"></span>
      <ul class="details">
        <li>
          <svg viewBox="0 0 24 24" aria-hidden="true"><path d="M6.6 10.8a15.1 15.1 0 0 0 6.6 6.6l2.2-2.2c.3-.3.7-.4 1-.2 1.1.4 2.3.6 3.6.6.6 0 1 .4 1 1V20c0 .6-.4 1-1 1A17 17 0 0 1 3 4c0-.6.4-1 1-1h3.5c.6 0 1 .4 1 1 0 1.3.2 2.5.6 3.6.1.3 0 .7-.2 1z"/></svg>
          0912 348765
        </li>
        <li>
          <svg viewBox="0 0 24 24" aria-hidden="true"><path d="M2 5h20v14H2zm2 2v.5l8 5 8-5V7l-8 5z"/></svg>
          info@lurvex.com
        </li>
      </ul>
    </div>
    <div class="front-address">00, Complex name, City, State 0042</div>
  </section>

  <section class="card card-back" aria-label="Business card back">
    <span class="brand-dot"></span>
    <span class="brand-name">lurvex</span>
  </section>
</main>
</body>
</html>
```